Business Card for a New Zealand IT Startup

I need a business card for VELTA Holdings. We are a young startup based in New Zealand working in internet marketing and web development. The design should have some element connected to New Zealand, such as wave, koru or silver fern, just don't use a kiwi bird.

```html
<!DOCTYPE html>
<html lang="en">
<head>
<meta charset="utf-8">
<title>VELTA Holdings – Business Card</title>
<link href="https://fonts.googleapis.com/css2?family=Jost:wght@400;500;600&display=swap" rel="stylesheet">
<style>
  :root {
    --backdrop: #1f1f1f;
    --brand-blue: #0070ba;
    --brand-orange: #f05a28;
    --paper: #ffffff;
  }
  html, body {
    margin: 0;
    padding: 0;
    width: 1125px;
    height: 1200px;
    overflow: hidden;
    background: var(--backdrop);
  }
  .card {
    position: absolute;
    left: 150px;
    width: 825px;
    height: 471px;
    border-radius: 26px;
    overflow: hidden;
  }
  .card--front { top: 98px; background: var(--paper); }
  .card--back { top: 631px; background: var(--brand-orange); }
  .card svg { display: block; width: 100%; height: 100%; }
  .type { font-family: "Jost", sans-serif; }
  .name { font-weight: 600; font-size: 30px; fill: var(--paper); }
  .role { font-weight: 600; font-size: 20px; fill: var(--paper); }
  .contact { font-weight: 400; font-size: 18.5px; fill: var(--paper); }
  .wordmark { font-weight: 600; fill: var(--brand-blue); }
  .wordmark--back { font-weight: 600; fill: var(--paper); }
  .web-back { font-weight: 400; font-size: 15px; letter-spacing: 6px; fill: var(--paper); opacity: .9; }
  .icon { fill: var(--paper); }
</style>
</head>
<body>

<section class="card card--front" aria-label="Front of business card">
  <svg viewBox="0 0 800 456" xmlns="http://www.w3.org/2000/svg">
    <path class="wave-orange" fill="var(--brand-orange)"
      d="M0 0 H800 V248 C788 338 700 360 600 326 C400 258 200 72 0 106 Z"/>
    <path class="wave-blue" fill="var(--brand-blue)" stroke="var(--paper)" stroke-width="1.5"
      d="M0 0 H800 V240 C768 306 662 304 572 284 C392 236 190 64 0 100 Z"/>

    <g class="type" text-anchor="end">
      <text class="name" x="757" y="64">MARK TANE</text>
      <text class="role" x="755" y="88">CEO/FOUNDER</text>
      <text class="contact" x="757" y="123">42 Harbourview Road</text>
      <text class="contact" x="757" y="148">Wellington, NZ 6011</text>
      <text class="contact" x="727" y="181">021 584 7730</text>
      <text class="contact" x="727" y="208">mark@veltaholdings.com</text>
      <text class="contact" x="727" y="233">www.veltaholdings.com</text>
    </g>

    <!-- phone -->
    <path class="icon" transform="translate(737 166)"
      d="M3 1 L6 0 L8.5 5 L6.5 7 C7.5 9.5 9.5 11.5 12 12.5 L14 10.5 L18 13 L17 16 C9 17 1 9 3 1 Z"/>
    <!-- envelope -->
    <g transform="translate(737 196)">
      <rect class="icon" width="18" height="13" rx="1.5"/>
      <path d="M1 1.5 L9 8 L17 1.5" fill="none" stroke="var(--brand-blue)" stroke-width="1.5"/>
    </g>
    <!-- globe -->
    <g transform="translate(746 226)">
      <circle class="icon" r="8.5"/>
      <path d="M-8.5 0 H8.5 M0 -8.5 C-4 -4 -4 4 0 8.5 M0 -8.5 C4 -4 4 4 0 8.5"
        fill="none" stroke="var(--brand-blue)" stroke-width="1.3"/>
    </g>

    <g class="type">
      <text class="wordmark" x="58" y="352" font-size="84" letter-spacing="2">VELTA</text>
      <text class="wordmark" x="60" y="400" font-size="30" letter-spacing="13">HOLDINGS</text>
    </g>
  </svg>
</section>

<section class="card card--back" aria-label="Back of business card">
  <svg viewBox="0 0 800 456" xmlns="http://www.w3.org/2000/svg">
    <circle cx="400" cy="210" r="118" fill="none" stroke="var(--paper)" stroke-width="22"/>
    <g class="type" text-anchor="middle">
      <text class="wordmark--back" x="400" y="212" font-size="40" letter-spacing="2">VELTA</text>
      <text class="wordmark--back" x="404" y="240" font-size="15" letter-spacing="6">HOLDINGS</text>
      <text class="web-back" x="400" y="398">www.veltaholdings.com</text>
    </g>
  </svg>
</section>

</body>
</html>
```